Business Card Design

We need a business card designed for a new company based in Melbourne called Kvt solutions. Kvt solutions provides management consulting specialising in the health and social services sector.

Kvt solutions offer a unique set of specialist skills │dealing with all levels of government │ unique communication skills│intimate knowledge of the health sector │solutions tailored to unique circumstances.

Kvt solutions takes on a select number of clients at any one time, this ensures that your organisation receives the attention required. On larger projects, Kvt solutions join up with other consultants to bring specialist skills to a project.
Updates

This is the first time I have used Pixel Harbor and thank you all for responding. The variation is amazing and makes it hard to decide. I have to ask some of my friends to give me their views. The response is fantastic. The one I pick will basically be the most visually appealing

Industry/Entity Type

Management Consulting

Contact Information for Business Card

Martin Oakes, Principal, Kvt solutions, 14 Wexcombe Ave, Larkdale VIC 3189, 0417 382 914, martino@kvtsolutions-example.com.au, www.kvtsolutions-example.com.au

```html
<!DOCTYPE html>
<html lang="en">
<head>
<meta charset="utf-8">
<title>Kvt solutions – Business Card</title>
<link rel="stylesheet" href="https://fonts.googleapis.com/css2?family=Open+Sans:wght@400;700&family=Roboto+Slab:wght@500&display=swap">
<style>
  :root {
    --backdrop: #4b4337;
    --card-red: #c8132b;
    --card-red-deep: #b10f25;
    --pattern-tint: rgba(255, 255, 255, 0.10);
    --ink-white: #ffffff;
    --card-shadow: rgba(0, 0, 0, 0.35);
  }
  * { margin: 0; padding: 0; box-sizing: border-box; }
  html, body {
    width: 1200px;
    height: 914px;
    overflow: hidden;
    background: var(--backdrop);
  }
  .business-card {
    position: absolute;
    left: 150px;
    top: 200px;
    width: 900px;
    height: 514px;
    background: linear-gradient(135deg, var(--card-red) 0%, var(--card-red-deep) 100%);
    box-shadow: 0 14px 40px var(--card-shadow);
    overflow: hidden;
    color: var(--ink-white);
  }
  .cross-pattern-area {
    position: absolute;
    right: 0;
    top: 0;
    width: 480px;
    height: 514px;
    background: linear-gradient(90deg, rgba(255,255,255,0) 0%, var(--pattern-tint) 45%, var(--pattern-tint) 100%);
  }
  .brand {
    position: absolute;
    left: 58px;
    top: 48px;
  }
  .brand-name {
    font-family: "Open Sans", sans-serif;
    font-weight: 700;
    font-size: 58px;
    line-height: 1;
    letter-spacing: 0.5px;
    color: var(--ink-white);
  }
  .brand-tagline {
    margin-top: 14px;
    font-family: "Roboto Slab", serif;
    font-weight: 500;
    font-size: 19px;
    letter-spacing: 1.2px;
    text-transform: uppercase;
    color: var(--ink-white);
  }
  .contact {
    position: absolute;
    left: 58px;
    top: 300px;
    font-family: "Open Sans", sans-serif;
  }
  .contact-name {
    font-size: 30px;
    font-weight: 700;
    margin-bottom: 12px;
  }
  .contact-role {
    font-weight: 400;
  }
  .contact-line {
    font-size: 21px;
    font-weight: 400;
    line-height: 1.4;
  }
</style>
</head>
<body>
  <main class="business-card">
    <div class="cross-pattern-area" role="img" aria-label="Decorative pattern of faint plus-shaped crosses across the right side of the card"></div>

    <header class="brand">
      <div class="brand-name">Kvt solutions</div>
      <div class="brand-tagline">Health &amp; Social Services Consulting</div>
    </header>

    <section class="contact">
      <p class="contact-name">Martin Oakes, <span class="contact-role">Principal</span></p>
      <p class="contact-line">Kvt solutions, 14 Wexcombe Ave,</p>
      <p class="contact-line">Larkdale VIC 3189, 0417 382 914,</p>
      <p class="contact-line">martino@kvtsolutions-example.com.au , www.kvtsolutions-example.com.au</p>
    </section>
  </main>
</body>
</html>
```